Business card design for a dynamic IT consulting company

We need a business card design for a young firm, specialized in the Telecommunications/Consulting industry. The name of the company is Quindor and Partners Business Consulting Ltd. (Short name: Quindor and Partnes)
Quindor = solve read reverse, so we aim to be uncomplicated and solution-oriented. The small pipe in our logo is also related to the word solve. So we need a new business card design, which is simple, eye catching and something non traditional (I would probably prefer a square shaped design rather than a rectangle, but open for suggestions). Attached our logo.

Target Market(s)

Usually our customers are Tier1 Telecoms providers (Q-Netra, Palorix, etc) and their executives.

Industry/Entity Type

Business

Contact Information for Business Card

Name: Bence Tolnavari
Email: b.tolnavari@quindor.hu
Web: www.quindor.hu
Mobile: +36 30 518 2769
Title: Managing Director

Optional:
Company name: Quindor and Partners Ltd.
Address: 1087 Budapest, Tolvenka str. 28/C, Hungary

Font styles to use
Other font styles liked:
• helveticaneue_medium, Prime Regular are used now.

Colors

Designer to choose colors to be used in the design.

Requirements
Must have
• I would like to have a 2 sided design.
Nice to have
• I thought if we make the logo a bit bigger (without the company name), that could go to the back with the company name below. I though, if the pipe in the logo is somehow touchable on the business card, would be nice and unique.

```html
<!DOCTYPE html>
<html lang="en">
<head>
<meta charset="utf-8">
<title>Quindor and Partners – Business Card</title>
<link rel="stylesheet" href="https://fonts.googleapis.com/css2?family=Roboto:wght@300;400;500;700&display=swap">
<style>
  :root {
    --canvas: #e9e7e3;
    --paper: #f4f4f4;
    --paper-shade: #e2e2e2;
    --charcoal: #353637;
    --charcoal-deep: #262728;
    --charcoal-soft: #4a4b4d;
    --rule: #8a8b8d;
    --azure: #1aa7d6;
    --azure-deep: #0f86b8;
    --ink-light: #ffffff;
    --ink-muted: #c9cacc;
    --logo-grey: #8c8d8f;
  }
  * { box-sizing: border-box; margin: 0; padding: 0; }
  html, body { width: 1200px; height: 780px; overflow: hidden; }
  body {
    background: var(--canvas);
    font-family: "Roboto", "Helvetica Neue", Arial, sans-serif;
    display: flex;
    align-items: center;
    justify-content: center;
    gap: 40px;
  }
  .card {
    width: 540px;
    height: 310px;
    border-radius: 4px;
    overflow: hidden;
    box-shadow: 0 10px 28px rgba(0,0,0,.22);
    position: relative;
  }

  /* Front side */
  .card--front { display: flex; flex-direction: column; }
  .front__brand {
    height: 148px;
    background: linear-gradient(180deg, var(--paper), var(--paper-shade));
    display: flex;
    align-items: center;
    padding-left: 70px;
    gap: 16px;
  }
  .brand__square {
    width: 18px; height: 18px;
    background: var(--azure);
  }
  .brand__name {
    font-size: 40px;
    font-weight: 300;
    color: var(--logo-grey);
    letter-spacing: .5px;
  }
  .front__contact {
    flex: 1;
    background: linear-gradient(180deg, var(--charcoal-soft), var(--charcoal));
    display: flex;
    align-items: center;
    padding: 0 36px;
  }
  .person { flex: 0 0 220px; text-align: right; padding-right: 24px; }
  .person__name { color: var(--ink-light); font-size: 20px; font-weight: 500; }
  .person__title { color: var(--ink-muted); font-size: 13px; margin-top: 4px; }
  .contact__divider { width: 1px; height: 74px; background: var(--rule); }
  .contact__list { list-style: none; padding-left: 22px; }
  .contact__item {
    display: flex; align-items: center; gap: 9px;
    color: var(--ink-light); font-size: 13px; line-height: 24px;
  }
  .contact__icon { width: 16px; height: 16px; flex: none; }
  .front__rule { height: 5px; background: #d9dadb; }
  .front__address {
    height: 44px;
    background: linear-gradient(90deg, var(--azure), var(--azure-deep));
    color: var(--ink-light);
    font-size: 14px;
    display: flex; align-items: center;
    padding-left: 62px;
  }

  /* Back side */
  .card--back {
    background: radial-gradient(ellipse at 30% 35%, #48494b 0%, var(--charcoal) 55%, var(--charcoal-deep) 100%);
    display: flex; flex-direction: column; align-items: center; justify-content: center;
    gap: 22px;
  }
  .back__brand { display: flex; align-items: center; gap: 14px; }
  .back__brand .brand__name { color: #d6d7d9; font-size: 38px; }
  .back__web { color: var(--ink-muted); font-size: 13px; letter-spacing: 3px; }
</style>
</head>
<body>

  <section class="card card--front" aria-label="Business card front">
    <header class="front__brand">
      <span class="brand__square"></span>
      <span class="brand__name">Quindor &amp; Partners</span>
    </header>

    <div class="front__contact">
      <div class="person">
        <p class="person__name">Bence Tolnavari</p>
        <p class="person__title">Managing Director</p>
      </div>
      <span class="contact__divider"></span>
      <ul class="contact__list">
        <li class="contact__item">
          <svg class="contact__icon" viewBox="0 0 16 16" aria-hidden="true">
            <circle cx="8" cy="8" r="7.5" fill="none" stroke="#fff" stroke-width="1"/>
            <rect x="5.5" y="3.8" width="5" height="8.4" rx="1" fill="none" stroke="#fff" stroke-width="1"/>
          </svg>
          +36 30 518 2769
        </li>
        <li class="contact__item">
          <svg class="contact__icon" viewBox="0 0 16 16" aria-hidden="true">
            <circle cx="8" cy="8" r="7.5" fill="#fff"/>
            <rect x="4" y="5.3" width="8" height="5.6" fill="none" stroke="#353637" stroke-width="1"/>
            <path d="M4 5.3 L8 8.6 L12 5.3" fill="none" stroke="#353637" stroke-width="1"/>
          </svg>
          b.tolnavari@quindor.hu
        </li>
        <li class="contact__item">
          <svg class="contact__icon" viewBox="0 0 16 16" aria-hidden="true">
            <circle cx="8" cy="8" r="7.5" fill="#fff"/>
            <circle cx="8" cy="8" r="4.5" fill="none" stroke="#353637" stroke-width="1"/>
            <ellipse cx="8" cy="8" rx="2" ry="4.5" fill="none" stroke="#353637" stroke-width="1"/>
            <path d="M3.5 8 H12.5" stroke="#353637" stroke-width="1"/>
          </svg>
          www.quindor.hu
        </li>
      </ul>
    </div>

    <div class="front__rule"></div>
    <footer class="front__address">1087 Budapest, Tolvenka str. 28/C, Hungary</footer>
  </section>

  <section class="card card--back" aria-label="Business card back">
    <div class="back__brand">
      <span class="brand__square"></span>
      <span class="brand__name">Quindor &amp; Partners</span>
    </div>
    <p class="back__web">www.quindor.hu</p>
  </section>

</body>
</html>
```